Varelko App for Smart Devices IoT WiFi Electronic

Varelko is a siren manufacturer. This application is used for the company's products that have a Wi-Fi connection and an internet connection, which can be configured and activated remotely through this application. In addition, this application is used to activate the siren at specific times for the start and end of shifts in companies and schools. Users will be siren installers and IT or HR managers.
In addition to activating motorized sirens timers, some siren models have speakers and allow you to play TTS (text to speech) audio, audio recorded by the user on the phone and upload audio (mp3) with playlist programming with start and end times.
Application screens: home with dashboard (one dashboard for each category). Device categories: timers, speakers, motorized siren. Screen for requesting evaluation in the Play Store. Screen for registering the user profile. Screen for registering devices according to their category (timers, speakers, motorized siren). Screen for registering device groups. Screen for pairing the device on the client's Wi-Fi network. Screen for registering activation times. Screen for uploading MP3 audios. Screen for registering playlists with audio selection, start and end times. Screen for recording audio for later sending to the speakers. Screen for converting text to speech and sending to the speakers. It is important to have a time picker with the day of the week to program the activation times and playlist.

Target Market(s)

Schools, Companies and Stores.

Industry/Entity Type

IoT

Font styles to use
Sans Serif
Other font styles liked:
• roboto

Colors
FFC000
F8CF3A
FAE287
FDF2CF
FEFAEE

Requirements
Must have
• time picker with weekdays for timer programming feature.
Nice to have
• app review request screen on play store

```html
<!DOCTYPE html>
<html lang="en">
<head>
<meta charset="utf-8">
<title>Varelko – Login</title>
<link rel="stylesheet" href="https://fonts.googleapis.com/css2?family=Poppins:ital,wght@0,400;0,500;0,600;1,800&display=swap">
<style>
  :root {
    --brand-yellow: #F7BE00;
    --brand-yellow-deep: #F1B300;
    --ink: #3F4656;
    --muted: #ABAFB8;
    --field-border: #E3E5EA;
    --ghost-title: #EEEFF2;
    --surface: #FFFFFF;
    --footer: #4B5667;
  }
  * { box-sizing: border-box; margin: 0; padding: 0; }
  html, body { width: 677px; height: 1200px; overflow: hidden; background: var(--surface); }
  body { font-family: "Poppins", sans-serif; color: var(--ink); }

  .screen { position: relative; width: 677px; height: 1200px; overflow: hidden; background: var(--surface); }

  .hero-shape { position: absolute; left: 0; top: 0; }

  .status-bar { position: absolute; top: 0; left: 0; right: 0; height: 70px; display: flex; align-items: center; justify-content: space-between; padding: 12px 34px 0 54px; }
  .status-time { font-weight: 600; font-size: 24px; color: var(--ink); letter-spacing: 0.2px; }
  .status-icons { display: flex; gap: 8px; align-items: center; }

  .tab-title { position: absolute; top: 138px; font-weight: 800; font-style: italic; font-size: 128px; line-height: 1; letter-spacing: -2px; }
  .tab-title--active { left: -4px; color: var(--surface); }
  .tab-title--inactive { left: 519px; color: var(--ghost-title); }

  .login-card { position: absolute; left: 35px; top: 394px; width: 607px; height: 438px; background: var(--surface); border-radius: 56px; box-shadow: 0 40px 90px rgba(60, 70, 90, 0.12), 0 6px 20px rgba(60, 70, 90, 0.05); padding: 97px 53px 0; }
  .field { display: flex; align-items: center; justify-content: space-between; height: 81px; border: 1.5px solid var(--field-border); border-radius: 41px; padding: 0 36px 0 41px; margin-bottom: 35px; }
  .field-value { font-weight: 500; font-size: 19px; color: var(--ink); }
  .field-value--secret { font-size: 28px; letter-spacing: 3px; padding-top: 8px; }
  .field-label { font-size: 16px; color: var(--muted); }

  .submit-button { position: absolute; left: 290px; top: 789px; width: 88px; height: 88px; border-radius: 50%; background: var(--brand-yellow); border: none; display: flex; align-items: center; justify-content: center; }

  .social-bar { position: absolute; left: 0; bottom: 0; width: 677px; height: 52px; background: var(--footer); display: flex; align-items: center; justify-content: center; gap: 12px; color: var(--surface); font-weight: 500; font-size: 20px; letter-spacing: 0.3px; }
  .social-mark { width: 20px; height: 20px; background: var(--surface); border-radius: 3px; }
</style>
</head>
<body>
<main class="screen">
  <svg class="hero-shape" width="677" height="600" viewBox="0 0 677 600" aria-hidden="true">
    <defs>
      <linearGradient id="heroFill" x1="0" y1="0" x2="0" y2="1">
        <stop offset="0" stop-color="#F8C000"/>
        <stop offset="1" stop-color="#F1B300"/>
      </linearGradient>
    </defs>
    <circle cx="114" cy="223" r="367" fill="url(#heroFill)"/>
  </svg>

  <header class="status-bar">
    <span class="status-time">9:41</span>
    <span class="status-icons">
      <svg width="26" height="16" viewBox="0 0 26 16" aria-hidden="true">
        <rect x="0" y="10" width="4" height="6" rx="1" fill="#3F4656"/>
        <rect x="7" y="7" width="4" height="9" rx="1" fill="#3F4656"/>
        <rect x="14" y="4" width="4" height="12" rx="1" fill="#3F4656"/>
        <rect x="21" y="0" width="4" height="16" rx="1" fill="#3F4656"/>
      </svg>
      <svg width="24" height="17" viewBox="0 0 24 17" aria-hidden="true">
        <path d="M12 17 8.5 13a5 5 0 0 1 7 0Z" fill="#3F4656"/>
        <path d="M4.6 9.4a10.5 10.5 0 0 1 14.8 0" stroke="#3F4656" stroke-width="2.6" fill="none" stroke-linecap="round"/>
        <path d="M1.4 5.6a15.5 15.5 0 0 1 21.2 0" stroke="#3F4656" stroke-width="2.6" fill="none" stroke-linecap="round"/>
      </svg>
      <svg width="36" height="17" viewBox="0 0 36 17" aria-hidden="true">
        <rect x="1" y="1" width="30" height="15" rx="4" stroke="#3F4656" stroke-opacity="0.4" stroke-width="1.5" fill="none"/>
        <rect x="3.5" y="3.5" width="25" height="10" rx="2.5" fill="#3F4656"/>
        <rect x="33" y="5.5" width="2" height="6" rx="1" fill="#3F4656" fill-opacity="0.4"/>
      </svg>
    </span>
  </header>

  <h1 class="tab-title tab-title--active">Login</h1>
  <span class="tab-title tab-title--inactive">Sig</span>

  <form class="login-card">
    <div class="field">
      <span class="field-value">diponto@varelko.com</span>
      <span class="field-label">Email</span>
    </div>
    <div class="field">
      <span class="field-value field-value--secret">*********</span>
      <span class="field-label">Password</span>
    </div>
  </form>

  <button class="submit-button" type="submit" aria-label="Log in">
    <svg width="34" height="24" viewBox="0 0 34 24" aria-hidden="true">
      <path d="M2 12h29M20 2l11 10-11 10" stroke="#FFFFFF" stroke-width="2.4" fill="none" stroke-linecap="round" stroke-linejoin="round"/>
    </svg>
  </button>

  <footer class="social-bar">
    <span class="social-mark"></span>
    <span class="social-name">LINKORA</span>
  </footer>
</main>
</body>
</html>
```